Ostrane Capital LLC

Need Professional Business cards for New Investment Fund

Target Market(s)

High Quality investors

Industry/Entity Type

Financial

Contact Information for Business Card

Phone Number +1 555 284 6190
Name Lukas Varenko
Title Fund Manager
email lv@FundOstrane.com
Website www.FundOstrane.com

Colors

Designer to choose colors to be used in the design.

Requirements
Must have
• Must have our Logo and all of the above. Must be made so lettering and loge can be raised

```html
<!DOCTYPE html>
<html lang="en">
<head>
<meta charset="utf-8">
<title>Ostrane Capital LLC — Business Card</title>
<link href="https://fonts.googleapis.com/css2?family=Raleway:wght@400;600;700&display=swap" rel="stylesheet">
<style>
  :root {
    --backdrop: #202020;
    --card-front: #434e43;
    --card-back: #121316;
    --green: #5bbd45;
    --grey-band: #3d463d;
    --white: #ffffff;
    --text-soft: #e8e8e8;
  }
  * { box-sizing: border-box; margin: 0; padding: 0; }
  html, body { width: 1200px; height: 900px; overflow: hidden; }
  body {
    background: var(--backdrop);
    font-family: "Raleway", sans-serif;
    position: relative;
  }
  .card {
    position: absolute;
    left: 270px;
    width: 660px;
    height: 377px;
    overflow: hidden;
  }
  .card--front { top: 42px; background: var(--card-front); }
  .card--back { top: 468px; background: var(--card-back); }

  /* Brand */
  .brand-mark {
    position: absolute;
    display: flex;
    align-items: center;
    gap: 12px;
    color: var(--white);
    font-weight: 600;
    letter-spacing: 3px;
    white-space: nowrap;
  }
  .brand-mark__square {
    width: 22px;
    height: 22px;
    background: var(--green);
    flex: none;
  }
  .card--front .brand-mark {
    left: 50%;
    top: 50%;
    transform: translate(-50%, -60%);
    font-size: 38px;
  }
  .card--front .brand-mark__square { width: 30px; height: 30px; }
  .front-bar {
    position: absolute;
    left: 240px;
    bottom: 0;
    width: 225px;
    height: 10px;
    background: var(--green);
  }

  /* Back */
  .card--back .brand-mark {
    right: 60px;
    top: 78px;
    font-size: 26px;
  }
  .divider {
    position: absolute;
    left: 120px;
    right: 66px;
    top: 190px;
    height: 2px;
    background: var(--green);
  }
  .name-tick {
    position: absolute;
    left: 36px;
    top: 200px;
    width: 9px;
    height: 40px;
    background: var(--green);
  }
  .holder {
    position: absolute;
    left: 95px;
    top: 202px;
  }
  .holder__name {
    color: var(--white);
    font-weight: 700;
    font-size: 24px;
    letter-spacing: 1.5px;
    text-transform: uppercase;
  }
  .holder__title {
    color: var(--text-soft);
    font-size: 17px;
    margin-top: 4px;
  }
  .contacts {
    position: absolute;
    right: 48px;
    top: 222px;
    list-style: none;
    text-align: right;
  }
  .contacts__item {
    display: flex;
    align-items: center;
    justify-content: flex-end;
    gap: 12px;
    color: var(--white);
    font-size: 19px;
    line-height: 28px;
  }
  .contacts__icon { width: 18px; height: 18px; flex: none; }
  .footer-bands {
    position: absolute;
    left: 0;
    bottom: 0;
    width: 660px;
    height: 60px;
  }
</style>
</head>
<body>
  <section class="card card--front" aria-label="Card front">
    <div class="brand-mark">
      <span class="brand-mark__square"></span>
      <span class="brand-mark__name">OSTRANE</span>
    </div>
    <div class="front-bar"></div>
  </section>

  <section class="card card--back" aria-label="Card back">
    <div class="brand-mark">
      <span class="brand-mark__square"></span>
      <span class="brand-mark__name">OSTRANE</span>
    </div>

    <div class="divider"></div>
    <div class="name-tick"></div>
    <div class="holder">
      <p class="holder__name">Lukas Varenko</p>
      <p class="holder__title">Title Fund Manager</p>
    </div>

    <ul class="contacts">
      <li class="contacts__item">+1 555 284 6190
        <svg class="contacts__icon" viewBox="0 0 24 24" aria-hidden="true"><path fill="#5bbd45" d="M6.6 10.8c1.4 2.8 3.8 5.1 6.6 6.6l2.2-2.2c.3-.3.7-.4 1-.2 1.1.4 2.3.6 3.6.6.6 0 1 .4 1 1V20c0 .6-.4 1-1 1C10.6 21 3 13.4 3 4c0-.6.4-1 1-1h3.5c.6 0 1 .4 1 1 0 1.3.2 2.5.6 3.6.1.3 0 .7-.2 1z"/></svg>
      </li>
      <li class="contacts__item">lv@FundOstrane.com
        <svg class="contacts__icon" viewBox="0 0 24 24" aria-hidden="true"><rect x="2.5" y="5" width="19" height="14" fill="none" stroke="#5bbd45" stroke-width="2"/><path d="M3 6l9 7 9-7" fill="none" stroke="#5bbd45" stroke-width="2"/></svg>
      </li>
      <li class="contacts__item">www.FundOstrane.com
        <svg class="contacts__icon" viewBox="0 0 24 24" aria-hidden="true"><g fill="none" stroke="#5bbd45" stroke-width="1.8"><circle cx="12" cy="12" r="9"/><ellipse cx="12" cy="12" rx="4" ry="9"/><path d="M3 12h18M5 7h14M5 17h14"/></g></svg>
      </li>
    </ul>

    <svg class="footer-bands" viewBox="0 0 660 60" aria-hidden="true">
      <polygon points="0,14 340,14 340,22 0,22" fill="#3d463d"/>
      <polygon points="352,22 380,4 660,4 660,26 392,26 380,34 352,34" fill="#5bbd45"/>
      <polygon points="390,40 660,40 660,50 382,50" fill="#5bbd45"/>
    </svg>
  </section>
</body>
</html>
```